American cannabis tech company business card design

Pavrel.com is seeking a modern, professional, and brand-aligned business card that represents our company and its core values: Mission, Story, Values, and Impact. As an innovative cannabis company, we want a business card that is not only visually appealing but also serves as a representation of who we are and what we stand for.

Project Scope: Design a double-sided business card that integrates our brand identity and core values. Incorporate our key brand elements, ensuring a sleek and contemporary aesthetic. Visually reflect our core values (Mission, Story, Values, Impact) in a way that is engaging yet professional.

Target Market(s)

Vendors, third parties,

Contact Information for Business Card

Contact details (name, title, email, phone, website, etc.)

Font styles to use
Other font styles liked:
• Caslon, Centra

Colors

Designer to choose colors to be used in the design.

Requirements
Must have
• Pavrel.com logo and branding A creative yet clean way to integrate our core values (Mission, Story, Values, Impact) Modern typography and a well-structured layout
Nice to have
• forest green, grey, white, black
Should not have
• references to marijuana, leafs, plants, or related product

```html
<!DOCTYPE html>
<html lang="en">
<head>
<meta charset="utf-8">
<title>Pavrel.com Business Card</title>
<link href="https://fonts.googleapis.com/css2?family=Playfair+Display:wght@700;900&family=Montserrat:wght@400;500&display=swap" rel="stylesheet">
<style>
  :root {
    --forest: #1a3320;
    --paper: #ffffff;
    --cream: #fbfaf6;
    --stage: #cfd4d4;
    --ink: #1f2a22;
  }
  * { margin: 0; padding: 0; box-sizing: border-box; }
  html, body { width: 1200px; height: 1050px; overflow: hidden; }
  body {
    background: var(--stage);
    display: flex;
    flex-direction: column;
    align-items: center;
    justify-content: center;
    gap: 50px;
  }
  .card {
    position: relative;
    width: 700px;
    height: 400px;
    overflow: hidden;
    box-shadow: 0 12px 30px rgba(0,0,0,0.18);
  }
  .card-front { background: var(--paper); }
  .card-back {
    background: var(--forest);
    display: flex;
    align-items: center;
    justify-content: center;
  }
  .wordmark {
    font-family: "Playfair Display", Georgia, serif;
    font-weight: 900;
    letter-spacing: 2px;
    line-height: 1;
  }
  .card-front .wordmark {
    position: absolute;
    top: 48px;
    left: 0;
    right: 0;
    text-align: center;
    font-size: 122px;
    color: var(--forest);
  }
  .card-back .wordmark {
    font-size: 138px;
    color: var(--cream);
  }
  .swoosh {
    position: absolute;
    inset: 0;
    width: 700px;
    height: 400px;
  }
  .contact-block {
    position: absolute;
    top: 224px;
    left: 190px;
    display: flex;
    align-items: stretch;
  }
  .person {
    text-align: right;
    padding-right: 14px;
    padding-top: 4px;
  }
  .person-name {
    font-family: "Playfair Display", Georgia, serif;
    font-weight: 700;
    font-size: 21px;
    color: var(--forest);
  }
  .person-title {
    font-family: "Playfair Display", Georgia, serif;
    font-weight: 700;
    font-size: 11px;
    color: var(--ink);
    margin-top: 2px;
  }
  .divider {
    width: 1px;
    background: var(--ink);
  }
  .contact-list {
    list-style: none;
    padding-left: 14px;
    font-family: "Montserrat", Arial, sans-serif;
    font-size: 14px;
    color: var(--ink);
  }
  .contact-list li {
    display: flex;
    align-items: center;
    gap: 9px;
    height: 24px;
  }
  .contact-list svg { width: 12px; height: 12px; fill: var(--forest); }
</style>
</head>
<body>
  <section class="card card-front">
    <svg class="swoosh" viewBox="0 0 700 400" aria-hidden="true">
      <path d="M0 262 Q300 372 700 400 L0 400 Z" fill="var(--forest)"/>
      <path d="M0 240 Q330 350 700 386 Q330 342 0 246 Z" fill="var(--forest)"/>
    </svg>
    <div class="wordmark">PAVREL</div>
    <div class="contact-block">
      <div class="person">
        <div class="person-name">Daniel Hart</div>
        <div class="person-title">Owner</div>
      </div>
      <div class="divider"></div>
      <ul class="contact-list">
        <li>
          <svg viewBox="0 0 24 24"><path d="M6.6 10.8a15.1 15.1 0 0 0 6.6 6.6l2.2-2.2a1 1 0 0 1 1-.25 11.4 11.4 0 0 0 3.6.57 1 1 0 0 1 1 1V20a1 1 0 0 1-1 1A17 17 0 0 1 3 4a1 1 0 0 1 1-1h3.5a1 1 0 0 1 1 1c0 1.25.2 2.45.57 3.57a1 1 0 0 1-.25 1z"/></svg>
          555-210-0148
        </li>
        <li>
          <svg viewBox="0 0 24 24"><path d="M2 5h20v14H2z M2 5l10 8 10-8" /></svg>
          info@pavrel.com
        </li>
        <li>
          <svg viewBox="0 0 24 24"><circle cx="12" cy="12" r="10"/></svg>
          www.pavrel.com
        </li>
      </ul>
    </div>
  </section>

  <section class="card card-back">
    <div class="wordmark">PAVREL</div>
  </section>
</body>
</html>
```